Mortgage and Asset Finance Broker Needs a Wordpress Website Design

I need a modern looking Wordpress website to showcase my service as a mortgage and asset broker. I have a company and we work with various lenders to arrange mortgages, as well as commercial lending and business asset finance. The website needs to look professional, be easy to navigate and capture leads. SEO is obviously very important to me. It really needs to be something that shows trust and professioanlism.
Updates

On the home page I will need to have some boxes for Home Loans, Refinancing, Business (and Agriculture) Loans etc. I'd like a carousel in the middle which shows our lenders (so that can have the banks logos added).

It needs to be easy top navigate and showcase all we do - Home Loans, Refinancing, Commercial Loans, Car Loans, Asset Finance etc.

There are plenty of companies on the internet that do this.

There is some good information here https://lendplatehq.com.au/mortgage-broker-homepage/

I need to make sure that editing the website is easy (I think Wordpress has something that allows that).

Also we are very much an Australian business so that is something to advertise.

Industry/Entity Type

Mortgage and Finance Broker

Coding

Coded - Design and coding required

Number of Pages Required

5+ page

Requirements
Must have
• Easy to navigate professional feel. Must be responsive and mobile friendly.
Nice to have
• Homepage with links to inner pages. Contact buttons.

```html
<!DOCTYPE html>
<html lang="en">
<head>
<meta charset="utf-8">
<title>Northvale Financial Services</title>
<link href="https://fonts.googleapis.com/css2?family=Montserrat:wght@400;500;600;700;800&display=swap" rel="stylesheet">
<style>
:root{
  --pink:#e0246b;
  --blue:#1262b8;
  --orange:#f7941d;
  --purple:#8d3b98;
  --dark:#1f1f1f;
  --ink:#1b1b1b;
  --muted:#6b6b6b;
  --blush:#fdf3f6;
  --white:#ffffff;
}
*{margin:0;padding:0;box-sizing:border-box}
html,body{width:1200px;height:3893px;overflow:hidden}
body{font-family:'Montserrat',sans-serif;color:var(--ink);background:var(--white);position:relative}
.abs{position:absolute}
.hex{clip-path:polygon(50% 0,100% 25%,100% 75%,50% 100%,0 75%,0 25%)}

/* buttons */
.btn{position:absolute;display:flex;align-items:center;height:40px;background:var(--blue);color:#fff;font-weight:700;font-size:15px;padding-left:18px;overflow:hidden;white-space:nowrap}
.btn::after{content:"";position:absolute;right:0;top:0;width:30px;height:100%;background:var(--orange);clip-path:polygon(30% 0,100% 0,100% 100%,0 100%)}
.btn .chev{position:absolute;right:8px;top:50%;transform:translateY(-50%);z-index:2;color:#fff;font-size:14px;font-weight:700}

/* header */
.site-header{position:absolute;left:0;top:0;width:1200px;height:80px;background:#fff;border-bottom:1px solid #e5e5e5}
.brand{position:absolute;left:143px;top:22px;display:flex;align-items:center;gap:8px;font-weight:800;font-size:26px;color:var(--ink)}
.brand-dot{width:14px;height:14px;background:var(--pink)}
.nav{position:absolute;top:32px;font-size:15px;color:#333}
.nav.active{color:var(--pink)}
.btn-call{left:896px;top:25px;width:159px;height:33px;font-size:14px;padding-left:12px}

/* hero */
.hero{position:absolute;left:0;top:80px;width:1200px;height:592px;background:linear-gradient(100deg,#3c4652 0%,#6d7a86 45%,#a7b3bd 70%,#cfd6dc 100%)}
.hero h1{position:absolute;left:143px;top:136px;font-size:50px;line-height:64px;font-weight:700;color:#fff;letter-spacing:1px}
.hero p{position:absolute;left:143px;top:272px;width:490px;font-size:18px;line-height:29px;color:#fff}
.hero .btn{left:143px;top:356px;width:160px;height:46px;font-size:16px}

/* lender strip */
.lender{position:absolute;top:728px;width:216px;height:72px;background:#fff;box-shadow:0 4px 14px rgba(0,0,0,.08);display:flex;align-items:center;justify-content:center}
.lender span{display:block;width:120px;height:20px;background:#2b2b2b;border-radius:3px}
.strip-arrow{position:absolute;top:751px;width:28px;height:28px;border-radius:50%;background:#fff;box-shadow:0 2px 8px rgba(0,0,0,.15);display:flex;align-items:center;justify-content:center;font-size:11px}

/* headings */
.eyebrow{position:absolute;left:0;width:1200px;text-align:center;font-size:13px;font-weight:500;color:var(--pink);letter-spacing:.5px}
.h2{position:absolute;left:0;width:1200px;text-align:center;font-size:35px;font-weight:700;letter-spacing:1px}
.lead{position:absolute;left:250px;width:700px;text-align:center;font-size:16px;line-height:28px}

/* intro */
.intro-bg{position:absolute;left:0;top:876px;width:720px;height:481px;background:var(--blush);clip-path:polygon(0 0,60% 0,100% 100%,0 100%)}
.body-text{position:absolute;font-size:13.5px;line-height:24px;color:var(--muted)}
.intro-photo{position:absolute;left:754px;top:1053px;width:353px;height:407px;background:linear-gradient(135deg,#d9dde1,#8c949c 60%,#5d656e)}

/* services */
.services{position:absolute;left:0;top:1498px;width:1200px;height:492px;background:var(--pink);overflow:hidden}
.services .eyebrow,.services .h2,.services .lead{color:#fff}
.svc{position:absolute;top:224px;width:166px;height:190px;background:#fff;display:flex;flex-direction:column;align-items:center;justify-content:center;gap:14px}
.svc .icon{width:62px;height:62px}
.svc p{font-size:14px;color:#333;white-space:nowrap}
.svc.featured{top:218px;width:178px;height:202px;gap:10px}
.svc .go{width:20px;height:20px}

/* news */
.news-bg{position:absolute;left:460px;top:2020px;width:740px;height:460px;background:#f8f4f8;clip-path:polygon(10% 0,100% 0,100% 100%,0 100%)}
.news-photo{position:absolute;top:2070px;height:375px;border-radius:8px;background:linear-gradient(135deg,#e6e8ea,#b9bfc5 55%,#6d737a)}
.news-arrow{position:absolute;top:2241px;width:32px;height:32px;border-radius:50%;display:flex;align-items:center;justify-content:center;font-size:14px;font-weight:700}
.meta{position:absolute;left:145px;top:2246px;font-size:13px;color:var(--purple)}

/* testimonials */
.avatar{position:absolute;background:linear-gradient(160deg,#c9ccd1,#5f6670)}
.main-avatar{position:absolute;left:544px;top:2670px;width:112px;height:128px;background:var(--pink);padding:5px}
.main-avatar div{width:100%;height:100%;background:#fff;padding:5px}
.main-avatar div div{background:linear-gradient(160deg,#9fb0c4,#34465c);padding:0}
.quote{position:absolute;left:280px;top:2815px;width:640px;text-align:center;font-size:13.5px;line-height:28px;color:var(--muted)}
.dot{position:absolute;top:2994px;height:5px;background:#ddd;border-radius:3px}

/* contact */
.contact{position:absolute;left:0;top:3078px;width:1200px;height:507px;background:var(--purple)}
.contact-photo{position:absolute;left:0;top:2935px;width:250px;height:595px;background:linear-gradient(160deg,#cfc6bd,#8e7f70 55%,#4a4040);clip-path:polygon(0 0,100% 37%,100% 87%,0 100%)}
.contact-frame{position:absolute;left:0;top:2920px;width:260px;height:625px;background:#fff;clip-path:polygon(0 0,100% 37%,100% 87%,0 100%,0 97%,96% 85%,96% 39%,0 3%)}
.field{position:absolute;border-bottom:1px solid rgba(255,255,255,.75);color:#fff;font-size:11px;padding-bottom:10px;display:flex;gap:6px;align-items:center}

/* footer */
.footer{position:absolute;left:0;top:3585px;width:1200px;height:308px;background:var(--dark);color:#fff}
.footer h4{position:absolute;top:58px;font-size:15px;font-weight:600;letter-spacing:.3px}
.footer ul{position:absolute;top:90px;list-style:none;font-size:13px;line-height:24px}
.social{position:absolute;top:191px;width:28px;height:28px;border-radius:50%;background:#fff}
</style>
</head>
<body>

<header class="site-header">
  <div class="brand"><span class="brand-dot"></span>northvale</div>
  <a class="nav active" style="left:365px">Home</a>
  <a class="nav" style="left:440px">About Us</a>
  <a class="nav" style="left:543px">Services</a>
  <a class="nav" style="left:638px">Features</a>
  <a class="nav" style="left:732px">Blog</a>
  <a class="nav" style="left:797px">Contact</a>
  <a class="btn btn-call">Schedule a Call<span class="chev">›</span></a>
</header>

<section class="hero" role="img" aria-label="Business professionals walking through a bright office corridor">
  <h1>NORTHVALE FINANCIAL<br>SERVICES</h1>
  <p>Lorem ipsum dolor sit amet, consectetur adipiscing elit,sed do eiusmod tempor incididunt</p>
  <a class="btn">Get Started<span class="chev">›</span></a>
</section>

<div class="strip-arrow" style="left:96px">◀</div>
<div class="lender" style="left:143px" aria-label="Lender partner"><span></span></div>
<div class="lender" style="left:373px" aria-label="Lender partner"><span></span></div>
<div class="lender" style="left:604px" aria-label="Lender partner"><span></span></div>
<div class="lender" style="left:836px" aria-label="Lender partner"><span></span></div>
<div class="strip-arrow" style="left:1074px">▶</div>

<section>
  <div class="intro-bg"></div>
  <div class="eyebrow" style="top:897px">INTRODUCTION</div>
  <h2 class="h2" style="top:922px">WHAT WE DO</h2>
  <p class="lead" style="top:977px">Duis aute irure dolor in reprehenderit in voluptate velit esse cillum dolore eu fugiat nulla pariatur. Excepteur sint occaecat cupidatat non proident.</p>
  <p class="body-text" style="left:145px;top:1074px;width:410px">Lorem ipsum dolor sit amet, consectetur adipiscing elit, sed do eiusmod tempor incididunt ut labore et dolore magna aliqua. Ut enim ad minim veniam, quis nostrud exercitation ullamco laboris nisi ut aliquip ex ea commodo consequat. Duis aute irure dolor in reprehenderit in voluptate velit esse cillum dolore eu fugiat nulla pariatur.</p>
  <a class="btn" style="left:143px;top:1251px;width:141px">Learn More<span class="chev">›</span></a>
  <div class="intro-photo hex" role="img" aria-label="Team meeting around a white table seen from above"></div>
</section>

<section class="services">
  <svg class="abs" style="left:0;top:0" width="1200" height="492"><path d="M196 0V492M1200 60L1000 200V492" stroke="rgba(255,255,255,.35)" fill="none"/></svg>
  <div class="eyebrow" style="top:57px;color:#fff">WHAT WE DO</div>
  <h2 class="h2" style="top:80px">NORTHVALE FINANCIAL SERVICES</h2>
  <p class="lead" style="top:135px">Duis aute irure dolor in reprehenderit in voluptate velit esse cillum dolore eu fugiat nulla pariatur. Excepteur sint occaecat cupidatat non proident.</p>

  <div class="svc hex" style="left:136px">
    <svg class="icon" viewBox="0 0 64 64" fill="none" stroke="#8d3b98" stroke-width="2.2"><path d="M16 30L32 16L48 30M20 27V42H44V27"/><circle cx="32" cy="32" r="5" stroke="#e0246b"/><path d="M8 52C18 46 26 48 34 52L52 46"/></svg>
    <p>Home Loans</p>
  </div>
  <div class="svc hex" style="left:322px">
    <svg class="icon" viewBox="0 0 64 64" fill="none" stroke="#8d3b98" stroke-width="2.2"><circle cx="32" cy="32" r="22" stroke="#e0246b"/><circle cx="32" cy="32" r="13"/><path d="M35 26H30a3 3 0 000 6h4a3 3 0 010 6h-6M32 23v18"/></svg>
    <p>Refinancing</p>
  </div>
  <div class="svc hex featured" style="left:511px">
    <svg class="icon" viewBox="0 0 64 64" fill="none" stroke="#8d3b98" stroke-width="2.2"><path d="M10 54H54M16 54V26H28V54M28 54V10H42V54M42 54V30H50V54"/><path d="M20 32h4M20 40h4M32 18h6M32 26h6M32 34h6"/></svg>
    <p>Commercial Loans</p>
    <svg class="go" viewBox="0 0 20 20"><circle cx="10" cy="10" r="8" fill="none" stroke="#f7941d" stroke-width="1.5"/><path d="M6 10H14M11 7L14 10L11 13" stroke="#f7941d" stroke-width="1.5" fill="none"/></svg>
  </div>
  <div class="svc hex" style="left:714px">
    <svg class="icon" viewBox="0 0 64 64" fill="none" stroke="#8d3b98" stroke-width="2.2"><circle cx="32" cy="16" r="9" stroke="#e0246b"/><path d="M12 44L18 32H46L52 44V52H12Z"/><circle cx="20" cy="44" r="3"/><circle cx="44" cy="44" r="3"/></svg>
    <p>Car Loans</p>
  </div>
  <div class="svc hex" style="left:900px">
    <svg class="icon" viewBox="0 0 64 64" fill="none" stroke="#8d3b98" stroke-width="2.2"><circle cx="34" cy="28" r="10" stroke="#e0246b"/><path d="M8 48C16 42 24 42 32 46H44L54 40"/><path d="M28 6v4M34 4v6M40 6v4" stroke="#e0246b"/></svg>
    <p>Asset Finance</p>
  </div>
</section>

<section>
  <div class="news-bg"></div>
  <div class="eyebrow" style="left:145px;width:auto;top:2098px">BLOG</div>
  <h2 class="h2" style="left:145px;width:auto;top:2122px">OUR NEWS</h2>
  <p class="abs" style="left:145px;top:2177px;width:420px;font-size:16px;line-height:28px">Duis aute irure dolor in reprehenderit in voluptate Excepteur sint occaecat cupidatat</p>
  <p class="meta">▦ July 25, 2024 &nbsp;&nbsp;&nbsp; ● By Mark Ellis,Lorem Ipsum dolor</p>
  <p class="body-text" style="left:145px;top:2274px;width:410px">Lorem ipsum dolor sit amet, consectetur adipiscing elit, sed do eiusmod tempor incididunt ut labore et dolore magna aliqua. Ut enim ad minim veniam,</p>
  <a class="btn" style="left:143px;top:2376px;width:141px">Learn More<span class="chev">›</span></a>
  <div class="news-photo" style="left:626px;width:406px" role="img" aria-label="Two colleagues reviewing reports at an office desk"></div>
  <div class="news-photo" style="left:1057px;width:160px" role="img" aria-label="Woman working at a calculator"></div>
  <div class="news-arrow" style="left:608px;background:#fff;color:var(--orange);box-shadow:0 2px 8px rgba(0,0,0,.12)">‹</div>
  <div class="news-arrow" style="left:1015px;background:var(--orange);color:#fff">›</div>
</section>

<section>
  <svg class="abs" style="left:0;top:2620px" width="1200" height="460"><path d="M160 160L260 100L360 160V300L260 360L160 300ZM1010 80L1140 20L1200 50M0 170L80 140" stroke="#eee" fill="none"/></svg>
  <div class="eyebrow" style="top:2578px;color:#e0462a">CLIENT FEEDBACK</div>
  <h2 class="h2" style="top:2603px">WHAT OUR CLIENT SAYS</h2>
  <div class="avatar hex" style="left:230px;top:2720px;width:56px;height:64px" role="img" aria-label="Client portrait"></div>
  <div class="avatar hex" style="left:818px;top:2740px;width:38px;height:44px" role="img" aria-label="Client portrait"></div>
  <div class="avatar hex" style="left:993px;top:2680px;width:60px;height:68px" role="img" aria-label="Client portrait"></div>
  <div class="avatar hex" style="left:145px;top:2860px;width:38px;height:44px" role="img" aria-label="Client portrait"></div>
  <div class="avatar hex" style="left:356px;top:2912px;width:40px;height:46px" role="img" aria-label="Client portrait"></div>
  <div class="avatar hex" style="left:824px;top:2905px;width:56px;height:64px" role="img" aria-label="Client portrait"></div>
  <div class="main-avatar hex"><div class="hex"><div class="hex" style="width:100%;height:100%" role="img" aria-label="Featured client portrait"></div></div></div>
  <p class="quote">Lorem ipsum dolor sit amet, consectetur adipiscing elit, sed do eiusmod tempor incididunt ut labore et dolore magna aliqua. Ut enim ad minim veniam, quis nostrud exercitation ullamco laboris nisi ut aliquip ex ea commodo consequat.</p>
  <p class="abs" style="left:0;width:1200px;text-align:center;top:2920px;font-size:17px;font-weight:500">Daniel Hartley</p>
  <p class="abs" style="left:0;width:1200px;text-align:center;top:2950px;font-size:11px;color:#e0462a">Lorem Ipsum</p>
  <span class="dot" style="left:549px;width:28px;background:var(--orange)"></span>
  <span class="dot" style="left:588px;width:16px"></span>
  <span class="dot" style="left:610px;width:16px"></span>
  <span class="dot" style="left:633px;width:16px"></span>
</section>

<section class="contact">
  <p class="abs" style="left:493px;top:52px;color:#fff;font-size:16px">Get In Touch</p>
  <h2 class="abs" style="left:493px;top:80px;color:#fff;font-size:38px;font-weight:700">Contact Us Today</h2>
  <div class="field" style="left:497px;top:153px;width:260px">⚲ First Name</div>
  <div class="field" style="left:794px;top:153px;width:260px">⚲ Last Name</div>
  <div class="field" style="left:497px;top:223px;width:260px">✉ Email Address</div>
  <div class="field" style="left:794px;top:223px;width:260px">✆ Phone Number</div>
  <div class="field" style="left:497px;top:292px;width:557px;height:70px;align-items:flex-start">✎ Message</div>
  <a class="btn" style="left:497px;top:402px;width:140px;background:#fff;color:var(--blue)">Submit Now<span class="chev">›</span></a>
</section>
<div class="contact-frame"></div>
<div class="contact-photo" role="img" aria-label="Smiling senior couple looking at a tablet"></div>

<footer class="footer">
  <div class="brand" style="top:98px;color:#fff;font-size:40px"><span class="brand-dot" style="width:18px;height:18px"></span>northvale</div>
  <h4 style="left:386px">QUICK LINKS</h4>
  <ul style="left:386px"><li>Home</li><li>About Us</li><li>Services</li><li>Projects</li><li>Contact</li><li>Schedule A Call</li></ul>
  <h4 style="left:582px">OTHER LINKS</h4>
  <ul style="left:582px"><li>Terms of Services</li><li>Terms &amp; Condition</li><li>Privacy Policy</li></ul>
  <span class="social" style="left:583px;background:var(--orange)" aria-label="Social profile"></span>
  <span class="social" style="left:618px" aria-label="Social profile"></span>
  <span class="social" style="left:655px" aria-label="Social profile"></span>
  <h4 style="left:794px">SUBSCRIBE FOR UPDATES</h4>
  <div class="abs" style="left:794px;top:92px;width:260px;height:40px;background:#fff;border-radius:3px;font-size:10px;color:#999;padding:14px 16px">Email Address<svg class="abs" style="right:14px;top:12px" width="16" height="16" viewBox="0 0 16 16"><path d="M1 8L15 1L11 15L8 9Z" fill="none" stroke="#e0246b" stroke-width="1.4"/></svg></div>
  <p class="abs" style="left:794px;top:155px;font-size:14px"><span style="color:var(--orange)">✉</span>&nbsp; <b style="font-weight:500">Email :</b>&nbsp; info@northvale.com.au</p>
  <p class="abs" style="left:794px;top:183px;font-size:14px"><span style="color:var(--orange)">✆</span>&nbsp; <b style="font-weight:500">Phone :</b>&nbsp; 1300-555-019</p>
  <div class="abs" style="left:1072px;top:232px;width:32px;height:32px;border-radius:50%;background:var(--pink);color:#fff;display:flex;align-items:center;justify-content:center;font-size:14px">⌃</div>
  <p class="abs" style="left:0;width:1200px;text-align:center;top:266px;font-size:12px">2025 Copyright - Northvale Financial Services | All Rights Reserved</p>
</footer>

</body>
</html>
```